Simple Logo Design for Semi-Clear Plastic Frosted Card stock

Create a business card on frosted plastic. compliment existing logo elements with a tree trunk, roots, or seed at the lower half and the full logo both on the front.

Contact information will go on a solid portion of the back of this design since this card stock is semi-transparent.

It is important to consider this plastic card stock medium in your design. I found helpful tips and guides listed at vellaprint-sample.net: be careful to understand ink printed on plastic cards cannot have too much of a consistent print area or risks peeling and fine lines can easily scratch off.
Updates

2" x 3.5" 20PT Clear Plastic Business cards with Round corners Please get info or templates here: https://www.vellaprint-sample.net/product-detail/2-x-35-20pt-clear-plastic-business-cards-with-round-corners

Target Market(s)

Not for profit- religion

Industry/Entity Type

Business

Must include complementary elements to the existing logo

Font styles to use
Decorative

Colors
000000

Requirements
Must have
• Elements of community, nature and oneness. Such as: seed, roots, tree trunk, etc.
• Three lines of space on the back for Name, Title, Phone Number.
Nice to have
• I like a light use of decorative elements
Should not have
• No eyes, from faces or animals.

```html
<!DOCTYPE html>
<html lang="en">
<head>
<meta charset="utf-8">
<title>Rooted Way – Business Card</title>
<link href="https://fonts.googleapis.com/css2?family=Open+Sans:wght@400;600;700&display=swap" rel="stylesheet">
<style>
  :root {
    --teal: #236c69;
    --green: #4a993f;
    --white: #ffffff;
    --backdrop: #e9ecea;
  }
  * { margin: 0; padding: 0; box-sizing: border-box; }
  html, body {
    width: 1200px;
    height: 900px;
    overflow: hidden;
    background: var(--backdrop);
    font-family: "Open Sans", Arial, sans-serif;
  }
  .card {
    position: absolute;
    left: 73px;
    top: 122px;
    width: 1054px;
    height: 655px;
  }
  .card-shape {
    position: absolute;
    inset: 0;
    width: 1054px;
    height: 655px;
  }
  .holder-name {
    position: absolute;
    left: 58px;
    top: 48px;
    color: var(--white);
    font-weight: 700;
    font-size: 37px;
    line-height: 1;
  }
  .holder-title {
    position: absolute;
    left: 58px;
    top: 100px;
    color: var(--white);
    font-weight: 400;
    font-size: 25px;
    line-height: 1;
  }
  .holder-phone {
    position: absolute;
    left: 58px;
    top: 554px;
    color: var(--white);
    font-size: 26px;
    line-height: 1;
    display: flex;
    align-items: center;
    gap: 8px;
  }
  .holder-phone svg { width: 22px; height: 22px; }
  .brand-name {
    position: absolute;
    left: 727px;
    top: 328px;
    transform: translateX(-50%);
    color: var(--teal);
    font-weight: 400;
    font-size: 58px;
    letter-spacing: 1px;
    line-height: 1;
    white-space: nowrap;
  }
</style>
</head>
<body>
  <div class="card">
    <svg class="card-shape" viewBox="0 0 1054 655" aria-hidden="true">
      <defs>
        <clipPath id="card-outline">
          <rect x="0" y="0" width="727" height="655"/>
          <circle cx="727" cy="327.5" r="327"/>
        </clipPath>
      </defs>
      <g clip-path="url(#card-outline)">
        <rect class="band-top" x="0" y="0" width="1054" height="180" fill="var(--teal)"/>
        <rect class="band-middle" x="0" y="180" width="1054" height="296" fill="var(--white)"/>
        <rect class="band-bottom" x="0" y="476" width="1054" height="179" fill="var(--green)"/>
        <circle class="logo-disc" cx="727" cy="327.5" r="320" fill="var(--white)"/>
        <path class="ring-upper" d="M 403 327.5 A 324 324 0 0 1 1051 327.5" fill="none" stroke="var(--teal)" stroke-width="8"/>
        <path class="ring-lower" d="M 1051 327.5 A 324 324 0 0 1 403 327.5" fill="none" stroke="var(--green)" stroke-width="8"/>
      </g>
    </svg>

    <div class="holder-name">Daniel Hartley</div>
    <div class="holder-title">Managing Director</div>
    <div class="holder-phone">
      <svg viewBox="0 0 24 24" aria-hidden="true"><path fill="#ffffff" d="M6.6 10.8a15.1 15.1 0 0 0 6.6 6.6l2.2-2.2a1 1 0 0 1 1-.25 11.4 11.4 0 0 0 3.6.57 1 1 0 0 1 1 1V20a1 1 0 0 1-1 1A17 17 0 0 1 3 4a1 1 0 0 1 1-1h3.5a1 1 0 0 1 1 1c0 1.25.2 2.45.57 3.57a1 1 0 0 1-.25 1z"/></svg>
      <span>(055)-312-4870</span>
    </div>

    <div class="brand-name">ROOTEDWAY</div>
  </div>
</body>
</html>
```